Locksmith Business Cards

My father-in-law is in need of new business cards for his locksmith business and I need to impress him. Kindly help me out!

You can see the previous business card attached. It is a family run business in North Wales.

No individual names on the cards.

Key Things to Feature:
- The words "Prompt", "Local", "Reliable" (as you can see under the logo on the website)
- 24h Emergency Service
- Covering All of North Wales, the Wirral and Chester
- The color blue
- A key or a lock would be interesting (similar to the ones that come up when you google locksmith business card)

Optional (only if design includes bullet points, like the example below):
https://imgvaultcdn.net/samples/208314/55172/55172_3904821_208314_image.jpg
- Residential / Commercial / Automotive
- Alarms & Cameras
- Key Cutting & Safes

https://www.brynhafod-locksmiths.co.uk/

Industry/Entity Type

Locksmith

Contact Information for Business Card

01632 960 418
07700 900 362
brynhafodlocksmiths@mailvane.com
Brynhafod Locksmiths, The Willow Barn, 7 Tannery Rd., Llandudno LL99 4QX
www.brynhafod-locksmiths.co.uk

Requirements
Must have
• - The words "Prompt", "Local", "Reliable" (as you can see under the logo on the website)
• - 24h Emergency Service
• - Covering All of North Wales, the Wirral and Chester
Nice to have
• - A key or a lock would be interesting (similar to the ones that come up when you google locksmith business card)

```html
<!DOCTYPE html>
<html lang="en">
<head>
<meta charset="utf-8">
<title>Brynhafod Locksmiths – Business Card</title>
<link href="https://fonts.googleapis.com/css2?family=Oswald:wght@400&family=Saira+Semi+Condensed:wght@400;500&family=Montserrat:wght@500&display=swap" rel="stylesheet">
<style>
  :root {
    --backdrop: #e8e5e0;
    --card-deep: #262f78;
    --card-mid: #34418f;
    --card-light: #3f4e9f;
    --band: rgba(120, 135, 200, 0.35);
    --ink-cream: #ece4d6;
    --ink-band: #cdd0e2;
    --accent: #2f93d6;
  }
  * { margin: 0; padding: 0; box-sizing: border-box; }
  html, body { width: 1200px; height: 1054px; overflow: hidden; }
  body { background: var(--backdrop); position: relative; }

  .card {
    position: absolute; left: 100px; top: 225px;
    width: 1000px; height: 603px;
    background: linear-gradient(135deg, var(--card-deep) 0%, var(--card-mid) 55%, var(--card-light) 100%);
    border-radius: 4px;
    overflow: hidden;
    box-shadow: 0 18px 40px rgba(20, 25, 60, 0.25);
  }

  .brand {
    position: absolute; left: 262px; top: 64px;
    display: flex; align-items: center; gap: 26px;
  }
  .brand-dot { width: 96px; height: 96px; border-radius: 50%; background: var(--ink-cream); flex: none; }
  .brand-name {
    font-family: "Oswald", sans-serif; font-weight: 400;
    color: var(--ink-cream);
    font-size: 76px; line-height: 76px; letter-spacing: 1px;
    text-transform: uppercase;
  }

  .contact-list, .service-list {
    position: absolute; list-style: none;
    font-family: "Saira Semi Condensed", sans-serif; font-weight: 500;
    color: var(--ink-cream); font-size: 26px; line-height: 34.8px;
  }
  .contact-list { left: 72px; top: 274px; }
  .service-list { left: 508px; top: 274px; }
  .contact-list li, .service-list li { display: flex; align-items: flex-start; }
  .contact-icon { width: 20px; height: 20px; margin: 7px 17px 0 0; flex: none; fill: var(--accent); }
  .service-list li::before {
    content: ""; width: 9px; height: 9px; border-radius: 50%;
    background: var(--accent); margin: 12px 25px 0 0; flex: none;
  }

  .tagline-band {
    position: absolute; left: 0; right: 0; bottom: 0; height: 63px;
    background: var(--band);
    display: flex; align-items: center; justify-content: center;
    font-family: "Montserrat", sans-serif; font-weight: 500;
    font-size: 21px; letter-spacing: 2px; color: var(--ink-band);
  }
  .tagline-band .sep { margin: 0 16px; }
</style>
</head>
<body>
  <main class="card">
    <div class="brand">
      <span class="brand-dot"></span>
      <span class="brand-name">Brynhafod<br>Locksmiths</span>
    </div>

    <ul class="contact-list">
      <li><svg class="contact-icon" viewBox="0 0 20 20"><path d="M3 9c0-4 3-6 7-6s7 2 7 6h-4V7H7v2zM5 11h10l2 6H3z"/></svg>01632 960 418</li>
      <li><svg class="contact-icon" viewBox="0 0 20 20"><path d="M3 9c0-4 3-6 7-6s7 2 7 6h-4V7H7v2zM5 11h10l2 6H3z"/></svg>07700 900 362</li>
      <li><svg class="contact-icon" viewBox="0 0 20 20"><path d="M1 4h18v12H1zM2 5l8 6 8-6" stroke="#262f78" stroke-width="1.5"/></svg>brynhafodlocksmiths@mailvane.com</li>
      <li><svg class="contact-icon" viewBox="0 0 20 20"><circle cx="10" cy="10" r="9"/><path d="M1 10h18M10 1c-4 4-4 14 0 18M10 1c4 4 4 14 0 18" stroke="#262f78" stroke-width="1.2" fill="none"/></svg>www.brynhafod-locksmiths.co.uk</li>
      <li><svg class="contact-icon" viewBox="0 0 20 20"><path d="M10 1a6 6 0 0 1 6 6c0 5-6 12-6 12S4 12 4 7a6 6 0 0 1 6-6z"/><circle cx="10" cy="7" r="2.3" fill="#262f78"/></svg>The Willow Barn, 7 Tannery Rd.,<br>Llandudno LL99 4QX</li>
    </ul>

    <ul class="service-list">
      <li>24h Emergency Service</li>
      <li>Covering All of North Wales,<br>the Wirral and Chester</li>
      <li>Residential / Commercial / Automotive</li>
      <li>Alarms &amp; Cameras</li>
      <li>Key Cutting &amp; Safes</li>
    </ul>

    <footer class="tagline-band">
      PROMPT<span class="sep">|</span>LOCAL<span class="sep">|</span>RELIABLE
    </footer>
  </main>
</body>
</html>
```